New Business Card Design Project

Use the flyer uploaded and website www.brightoakbuilders.com for inspiration.
List Our Services on Backside of business cards
Marcus Delling
Harborline Builders Inc.
Licensed General Contractors
858-471-6093

Contact Information for Business Card

Use the flyer uploaded and website www.brightoakbuilders.com for inspiration. List Our Services on Backside of business cards Marcus Delling Harborline Builders Inc. Licensed General Contractors 858-471-6093

```html
<!DOCTYPE html>
<html lang="en">
<head>
<meta charset="utf-8">
<title>Harborline Builders – Business Card</title>
<link rel="stylesheet" href="https://fonts.googleapis.com/css2?family=Marcellus&family=Montserrat:wght@400;500;600;700&display=swap">
<style>
  :root {
    --backdrop: #e9e8e9;
    --card: #151515;
    --ink: #ffffff;
    --ink-soft: #e6e6e6;
    --rule: #cfcfcf;
  }
  * { margin: 0; padding: 0; box-sizing: border-box; }
  html, body { width: 1200px; height: 1108px; overflow: hidden; }
  body {
    position: relative;
    background: var(--backdrop);
    font-family: "Montserrat", sans-serif;
    color: var(--ink);
  }
  .card {
    position: absolute;
    width: 740px;
    height: 443px;
    background: var(--card);
    overflow: hidden;
  }
  .card--front { left: 241px; top: 68px; }
  .card--back  { left: 248px; top: 589px; }

  .brand-name {
    position: absolute;
    font-family: "Marcellus", serif;
    font-weight: 400;
    color: var(--ink);
    letter-spacing: 1px;
    white-space: nowrap;
  }
  .card--front .brand-name { left: 27px; top: 46px; font-size: 30px; }
  .card--back .brand-name {
    left: 0; width: 356px; top: 204px; text-align: center; font-size: 25px;
  }

  .backdrop-art {
    position: absolute;
    left: 439px; top: 0; width: 301px; height: 443px;
    background: radial-gradient(ellipse at 55% 18%, #5c5c5c 0%, #2b2b2b 35%, #151515 70%);
  }

  .person { position: absolute; left: 41px; top: 200px; }
  .person__name { font-size: 27px; font-weight: 600; line-height: 1.2; }
  .person__title { font-size: 16px; font-weight: 400; color: var(--ink-soft); margin-top: 1px; }

  .contacts { position: absolute; left: 37px; top: 296px; list-style: none; }
  .contacts li {
    display: flex; align-items: center; height: 29.5px;
    font-size: 16.5px; color: var(--ink-soft);
  }
  .contacts svg { width: 16px; height: 16px; margin-right: 13px; fill: var(--ink); }

  .license { position: absolute; left: 36px; top: 400px; font-size: 16px; color: var(--ink-soft); }

  .divider {
    position: absolute; left: 356px; top: 111px; width: 2px; height: 262px;
    background: var(--rule);
  }
  .services { position: absolute; left: 384px; top: 105px; }
  .services__title { font-size: 22px; font-weight: 600; margin-bottom: 6px; }
  .services__list { list-style: none; }
  .services__list li {
    font-size: 17px; color: var(--ink-soft); line-height: 27.2px;
  }
  .services__list li::before { content: "\2022"; margin-right: 6px; color: var(--ink); }
</style>
</head>
<body>

<section class="card card--front" aria-label="Business card front">
  <div class="brand-name">HARBORLINE BUILDERS</div>
  <div class="backdrop-art" role="img" aria-label="Faint palm tree and house outline decoration"></div>

  <div class="person">
    <div class="person__name">Marcus Delling</div>
    <div class="person__title">Managing Director</div>
  </div>

  <ul class="contacts">
    <li>
      <svg viewBox="0 0 16 16" aria-hidden="true"><path d="M3 2h3l1 3-2 1.2a9 9 0 0 0 4.8 4.8L11 9l3 1v3a1 1 0 0 1-1 1A12 12 0 0 1 2 3a1 1 0 0 1 1-1z"/></svg>
      858-471-6093
    </li>
    <li>
      <svg viewBox="0 0 16 16" aria-hidden="true"><path d="M1 4h14v9H1z" /><path d="M1 4l7 5 7-5" fill="none" stroke="#151515" stroke-width="1.4"/></svg>
      info@brightoakbuilders.com
    </li>
    <li>
      <svg viewBox="0 0 16 16" aria-hidden="true"><circle cx="8" cy="8" r="7"/><path d="M1 8h14M8 1c-3 3-3 11 0 14M8 1c3 3 3 11 0 14" fill="none" stroke="#151515" stroke-width="1.1"/></svg>
      www.brightoakbuilders.com
    </li>
  </ul>

  <div class="license">CLSB Licensed No #1048265</div>
</section>

<section class="card card--back" aria-label="Business card back">
  <div class="brand-name">HARBORLINE BUILDERS</div>
  <div class="divider"></div>
  <div class="services">
    <h2 class="services__title">Our Services</h2>
    <ul class="services__list">
      <li>Remodel: Kitchen &amp; Bath</li>
      <li>Painting: Interior &amp; Exterior</li>
      <li>Flooring: Carpet, Vinyl, Wood</li>
      <li>Window &amp; Door Replacement</li>
      <li>Plumbing: Repair &amp; Upgrades</li>
      <li>Energy Efficienct Upgrades</li>
      <li>Deck &amp; Patio construction</li>
      <li>Water &amp; Mold Damage</li>
      <li>Garage Renovation</li>
    </ul>
  </div>
</section>

</body>
</html>
```